Meridale Bed Company Needs Business Card

Looking for a very nice looking business card. Creative but not extravagant. We sell beds and pillows across the U.S. and need something professional but catchy. I have attached the logo.

Name : Devin Holt
Title : President
Phone : (800) 471-2960
Email: sleep@quilmora.com
Website: www.quilmora.com

Can be single-sided or double-sided
horizontal or vertical

Can use Blues/Greys

Target Market(s)

Mass Market

Industry/Entity Type

Retail

Contact Information for Business Card

Name : Devin Holt
Title : President
Phone : (800) 471-2960
Email: sleep@quilmora.com
Website: www.quilmora.com

Requirements
Must have
• Clean, Modern, Smooth
• Can use Blues/Greys
• On the other side without the information - have something simple like www.quilmora.com or our logo
Nice to have
• Surprise me
Should not have
• Nothing crazy, nothing cluttered

```html
<!DOCTYPE html>
<html lang="en">
<head>
<meta charset="utf-8">
<title>Quilmora Business Card – Devin Holt</title>
<link rel="stylesheet" href="https://fonts.googleapis.com/css2?family=Open+Sans:wght@400;600&display=swap">
<style>
  :root {
    --page-bg: #ecebe9;
    --card-bg: #363636;
    --accent-blue: #2ea3dc;
    --text-white: #ffffff;
    --card-shadow: rgba(0, 0, 0, 0.18);
  }
  * { margin: 0; padding: 0; box-sizing: border-box; }
  html, body {
    width: 1200px;
    height: 900px;
    overflow: hidden;
    background: var(--page-bg);
    font-family: "Open Sans", Arial, sans-serif;
  }
  .canvas {
    position: relative;
    width: 1200px;
    height: 900px;
  }
  .card {
    position: absolute;
    background: var(--card-bg);
    box-shadow: 0 6px 18px var(--card-shadow);
  }
  .card-front {
    left: 78px;
    top: 35px;
    width: 587px;
    height: 363px;
  }
  .card-back {
    left: 389px;
    top: 506px;
    width: 565px;
    height: 350px;
  }
  .contact-block {
    position: absolute;
    left: 0;
    width: 587px;
    top: 90px;
    padding-left: 0;
    text-align: center;
    transform: translateX(-1px);
  }
  .contact-block {
    left: 0;
    width: 586px;
  }
  .person-name {
    color: var(--accent-blue);
    font-weight: 600;
    font-size: 24px;
    line-height: 32px;
    margin-left: -0px;
  }
  .person-title {
    color: var(--text-white);
    font-size: 18px;
    line-height: 24px;
  }
  .divider {
    display: block;
    width: 130px;
    height: 1px;
    margin: 28px auto 30px;
    border-top: 1px dashed var(--accent-blue);
  }
  .contact-list {
    list-style: none;
    color: var(--text-white);
    font-size: 16px;
    line-height: 24.5px;
  }
  .brand-name {
    position: absolute;
    left: 0;
    width: 565px;
    top: 128px;
    text-align: center;
    color: var(--accent-blue);
    font-weight: 400;
    font-size: 68px;
    letter-spacing: 2px;
    line-height: 80px;
    padding-left: 0;
    transform: translateX(0);
  }
</style>
</head>
<body>
  <main class="canvas">
    <section class="card card-front" aria-label="Business card front">
      <div class="contact-block" style="left:-79px;width:742px;">
        <p class="person-name">Devin Holt</p>
        <p class="person-title">President</p>
        <span class="divider"></span>
        <ul class="contact-list">
          <li>(800) 471-2960</li>
          <li>sleep@quilmora.com</li>
          <li>www.quilmora.com</li>
        </ul>
      </div>
    </section>

    <section class="card card-back" aria-label="Business card back">
      <p class="brand-name" style="left:118px;width:330px;">quilmora</p>
    </section>
  </main>
</body>
</html>
```